Flyer, poster, banner and social media titles designs for Community Mending Chartre

The Harbourline Charter for Community Mending provide a nationally agreed framework to guide recovery policy and practice across Australia. The Principles support recovery practitioners, governments, non-government organisations and communities to deliver effective, community-centred recovery outcomes.
The Principles have recently been refreshed through extensive consultation and we require a contemporary visual identity and design suite that will increase awareness, engagement and practical application of the Principles.
The redesign will cover:
• A4 Brochure (primary publication)
• A3 Poster
• Pull up banner
• Social Media Tiles
The new design should:
• Create a recognisable brand for the Harbourline Charter.
• Appeal to both experienced and emerging recovery practitioners.
• Reflect contemporary disaster recovery practice.
• Feel people-focused rather than government-focused.
• Support future resources such as videos, implementation guides, presentations and workshop materials.
• Remain relevant for several years without requiring a major redesign.
Target Audience
• Disaster recovery practitioners
• Government agencies
• Non-government organisations
• Community recovery workers
• Recovery managers and leaders
• Community stakeholders and volunteers
The visual identity should reflect the six Principles:
• Understanding Context
• Recognising Complexity
• Community-Centred Approaches
• Coordination
• Communication
• Capacity Building
The design should communicate:
• Recovery is centred on people and communities.
• Recovery is collaborative and involves many sectors.
• Recovery is adaptive, inclusive and evidence-informed.
• Recovery supports resilience and long-term wellbeing.
• The Principles provide practical guidance for recovery practice.
We are looking for:
• Modern and professional
• Warm and approachable
• Human-centred
• Inclusive and accessible
• Australian in context
• Visually engaging
• Suitable for print and digital use
We would like to avoid:
• Images of disaster destruction
• Emergency response imagery (fire trucks, flashing lights, etc.)
• Overly corporate or bureaucratic designs
• Designs that focus on deficits rather than recovery and growth
Consider themes such as:
• Connection and collaboration
• Communities and people
• Growth, recovery and renewal
Accessibility
Designs should:
• Meet accessibility best practice
• Use clear typography
• Achieve strong colour contrast
• Be suitable for both digital and print formats

Deliverables
1. Principles Brochure
• A4 trifold size x 2 (online and print friendly version)
• A side to include cover side, logos side and overview of principles.
• B side full details of the principles
• Graphic to highlight the 3 c’s concept (RECOVERY Context, complexity, community centred, coordinate, communicate and capacity). Currently 3 circles.
• Can be printed and distributed electronically
2. Poster
• A1 and A3 versions
• Suitable for office and workshop display
3. Pull-Up Banner - 850 mm (W) × 2000 mm (H)
• Conference and event use
• High visual impact
• Strong branding and concise messaging
4. Social Media Tiles x 3

We are providing an extension and increasing the budget following feedback from designers. We are wanting the resources to look and feel different from the existing designs, considering either a different colour palette in the designs or different motif with the leave design. Any nature based designs should consider the Australian fauna or flora. Also suggest avoiding images in the designs. The principles are not numbered or liner in the concept of how they function. Happy to answer any further questions and thank you for your suggested concepts.

Disaster recovery practitioners, Government agencies , Non-government organisations, Community recovery workers and Community stakeholders and volunteers

Disaster recovery

• Modern, warm, visually engaging, human-centred, Australian in context and different to the current design.
• Symbols for each principles
• Images of disaster destruction, Emergency response imagery, Overly corporate or bureaucratic designs, Designs that focus on deficits rather than recovery and growth, avoid too much black

```html
<!DOCTYPE html>
<html lang="en">
<head>
<meta charset="utf-8">
<title>Harbourline Charter for Community Mending – Trifold Brochure</title>
<link rel="stylesheet" href="https://fonts.googleapis.com/css2?family=Oswald:wght@500;600;700&family=Cutive+Mono&family=Roboto:wght@400;700&display=swap">
<style>
  :root {
    --leaf: #6f9e2c;
    --leaf-pale: #e4edd6;
    --ink: #1f1f1f;
    --body: #333333;
    --muted: #8a8a8a;
    --paper: #ffffff;
    --night: #262626;
    --night-text: #e6e6e6;
  }
  * { box-sizing: border-box; margin: 0; padding: 0; }
  html, body { width: 849px; height: 1200px; overflow: hidden; background: #e9e9e9; }
  body { font-family: "Roboto", Arial, sans-serif; color: var(--body); }

  .canvas { position: relative; width: 849px; height: 1200px; }
  .side { position: absolute; left: 0; width: 849px; height: 600px; background: var(--paper); overflow: hidden; }
  .side-a { top: 0; }
  .side-b { top: 600px; border-top: 1px solid #dcdcdc; }

  .sprig-mark { display: block; width: 11px; height: 11px; border-radius: 50%; background: var(--leaf); }
  .kicker { font-family: "Cutive Mono", "Courier New", monospace; color: var(--leaf); font-size: 12.5px; line-height: 12.5px; }
  .headline { font-family: "Oswald", "Arial Narrow", sans-serif; font-weight: 700; color: var(--ink); text-transform: uppercase; }

  /* ---------- Side A : relationship panel ---------- */
  .relationship { position: absolute; left: 0; top: 0; width: 305px; height: 600px; }
  .relationship > .sprig-mark { position: absolute; left: 66px; top: 32px; }
  .relationship > .kicker { position: absolute; left: 57px; top: 55px; font-size: 14px; }
  .relationship > .headline { position: absolute; left: 57px; top: 67px; font-size: 19px; line-height: 24px; }
  .relationship .intro { position: absolute; left: 57px; top: 97px; width: 180px; font-size: 8.2px; line-height: 11.6px; text-align: justify; }
  .relationship .grid-title { position: absolute; left: 24px; top: 181px; width: 237px; text-align: center; font-family: "Cutive Mono", monospace; font-size: 13.5px; color: var(--ink); }

  .pillars { position: absolute; left: 24px; top: 202px; width: 237px; height: 368px;
    display: grid; grid-template-columns: 1fr 1fr; grid-template-rows: 130px 136px 102px; }
  .pillar { padding: 4px 4px 0 5px; }
  .pillar:nth-child(odd) { border-right: 1px dotted var(--muted); padding-left: 0; padding-right: 5px; }
  .pillar:nth-child(-n+4) { border-bottom: 1px dotted var(--muted); }
  .pillar:nth-child(n+3) { padding-top: 10px; }
  .pillar-head { display: flex; align-items: flex-end; gap: 4px; margin-bottom: 6px; }
  .pillar-head .sprig-mark { width: 9px; height: 9px; margin-bottom: 2px; flex: none; }
  .pillar-label { font-family: "Oswald", sans-serif; font-weight: 600; font-size: 10px; line-height: 11px; color: var(--ink); }
  .pillar-label .accent { color: var(--leaf); display: block; }
  .pillar p { font-size: 8.1px; line-height: 11.3px; }

  /* ---------- Side A : partners panel ---------- */
  .partners { position: absolute; left: 305px; top: 0; width: 260px; height: 600px; }
  .field-photo { position: absolute; left: 11px; top: 68px; width: 236px; height: 158px; border-radius: 16px 0 0 0;
    background: linear-gradient(120deg, #e8742a 0%, #d89447 45%, #8c7a63 80%, #6b5d4d 100%); }
  .partner-grid { position: absolute; left: 11px; top: 237px; width: 234px; height: 232px;
    display: grid; grid-template-columns: repeat(3, 1fr); grid-template-rows: repeat(4, 58px); }
  .partner { display: flex; align-items: center; justify-content: center; text-align: center; padding: 0 5px;
    font-size: 6.4px; line-height: 8px; color: var(--ink); border-right: 1px solid #e2e2e2; border-bottom: 1px solid #e2e2e2; }
  .partner:nth-child(3n) { border-right: none; }
  .partner:nth-child(n+10) { border-bottom: none; }
  .partners-box { position: absolute; left: 11px; top: 476px; width: 234px; height: 88px; border: 1px solid #a9a9a9; }
  .partners-box .headline { display: block; text-align: center; font-size: 10.5px; line-height: 13px; margin-top: 8px; }
  .partners-box .headline .accent { color: var(--leaf); }
  .reference-group { display: flex; align-items: center; justify-content: center; gap: 8px; margin-top: 16px; font-size: 10.5px; line-height: 13px; color: var(--ink); }
  .reference-group .dot { width: 26px; height: 26px; border-radius: 50%; background: #3fa9d6; flex: none; }

  /* ---------- Side A : cover panel ---------- */
  .cover { position: absolute; left: 565px; top: 0; width: 284px; height: 600px; background: var(--night); }
  .cover-photo { position: absolute; left: 120px; top: 50px; width: 164px; height: 550px;
    background: linear-gradient(90deg, var(--night) 0%, rgba(38,38,38,0) 38%),
                linear-gradient(180deg, #4a4742 0%, #6e5f4e 45%, #7d6c57 70%, #4f4337 100%); }
  .cover > .sprig-mark { position: absolute; left: 46px; top: 46px; width: 13px; height: 13px; }
  .cover > .kicker { position: absolute; left: 46px; top: 86px; font-size: 13px; line-height: 14px; }
  .cover > .headline { position: absolute; left: 46px; top: 121px; font-size: 30px; line-height: 32px; color: #ffffff; }
  .cover .rule { position: absolute; left: 46px; top: 192px; width: 118px; height: 2px; background: var(--leaf); }
  .cover .copy { position: absolute; left: 46px; top: 205px; width: 120px; }
  .cover .copy p { font-size: 8.3px; line-height: 11.2px; color: var(--night-text); margin-bottom: 11px; }

  /* ---------- Side B : principle columns ---------- */
  .principle { position: absolute; top: 10px; width: 112px; z-index: 1; }
  .principle .sprig-mark { margin: 0 0 9px 8px; }
  .principle .headline { font-size: 17px; line-height: 21px; font-weight: 600; letter-spacing: -0.2px; white-space: nowrap; margin: 1px 0 4px; }
  .principle .lead { font-size: 5.9px; line-height: 7.3px; font-weight: 700; color: var(--leaf); text-align: justify; margin-bottom: 10px; }
  .principle ul { list-style: none; }
  .principle li { position: relative; padding-left: 8px; font-size: 6.1px; line-height: 7.7px; margin-bottom: 7px; color: var(--body); }
  .principle li::before { content: ""; position: absolute; left: 0; top: 2.5px; width: 3px; height: 3px; border-radius: 50%; background: var(--leaf); }
  .p-context { left: 24px; }
  .p-complexity { left: 150px; }
  .p-community { left: 306px; }
  .p-coordinate { left: 433px; }
  .p-communicate { left: 588px; }
  .p-capacity { left: 715px; }

  .foliage { position: absolute; background: var(--leaf-pale); border-radius: 60% 40% 0 0; z-index: 0; }
  .foliage-1 { left: 16px; top: 422px; width: 118px; height: 178px; }
  .foliage-2 { left: 337px; top: 506px; width: 66px; height: 94px; }
  .foliage-3 { left: 568px; top: 430px; width: 124px; height: 170px; }
</style>
</head>
<body>
<main class="canvas">

  <section class="side side-a">
    <div class="relationship">
      <span class="sprig-mark" role="img" aria-label="Small green leaf sprig"></span>
      <p class="kicker">The relationship</p>
      <h2 class="headline">Between the principles</h2>
      <p class="intro">While all the principles are equally critical to ensure effective recovery, understanding the local and broader context and recognising complexity are foundational. The descriptions beneath each principle provide further guidance for working with communities in disaster recovery.</p>
      <p class="grid-title">Successful Recovery</p>
      <div class="pillars">
        <div class="pillar">
          <div class="pillar-head"><span class="sprig-mark" role="img" aria-label="Small green leaf sprig"></span><span class="pillar-label"><span class="accent">Understand</span>the CONTEXT</span></div>
          <p>Successful recovery is based on an understanding of the community context, with each community having its own history, values and dynamics.</p>
        </div>
        <div class="pillar">
          <div class="pillar-head"><span class="sprig-mark" role="img" aria-label="Small green leaf sprig"></span><span class="pillar-label"><span class="accent">Recognise</span>COMPLEXITY</span></div>
          <p>Successful recovery is responsive to the complex and evolving nature of disasters and their impacts on communities, including compounding, cascading and concurrent events.</p>
        </div>
        <div class="pillar">
          <div class="pillar-head"><span class="sprig-mark" role="img" aria-label="Small green leaf sprig"></span><span class="pillar-label"><span class="accent">Use COMMUNITY-</span>CENTRED approaches</span></div>
          <p>Successful recovery is community-centred, responsive and flexible, engaging with community and supporting them to move forward, with shared responsibilities.</p>
        </div>
        <div class="pillar">
          <div class="pillar-head"><span class="sprig-mark" role="img" aria-label="Small green leaf sprig"></span><span class="pillar-label"><span class="accent">COORDINATE</span>all activities</span></div>
          <p>Successful recovery requires a planned, coordinated and adaptive approach, between community and partner agencies, based on continuing assessment of impacts and needs.</p>
        </div>
        <div class="pillar">
          <div class="pillar-head"><span class="sprig-mark" role="img" aria-label="Small green leaf sprig"></span><span class="pillar-label"><span class="accent">COMMUNICATE</span>effectively</span></div>
          <p>Successful recovery is built on effective communication between the affected community and other partners.</p>
        </div>
        <div class="pillar">
          <div class="pillar-head"><span class="sprig-mark" role="img" aria-label="Small green leaf sprig"></span><span class="pillar-label"><span class="accent">Recognise and</span>build CAPACITY</span></div>
          <p>Successful recovery recognises, supports and builds on individual, community and organisational capacity and resilience.</p>
        </div>
      </div>
    </div>

    <div class="partners">
      <div class="field-photo" role="img" aria-label="Photograph of a smiling rescue worker in orange gear with a golden dog"></div>
      <div class="partner-grid">
        <div class="partner">Coastal Human Services Office</div>
        <div class="partner">Office of Home Matters</div>
        <div class="partner">Open Hands Aid</div>
        <div class="partner">Southland Government</div>
        <div class="partner">Westland Government</div>
        <div class="partner">Isle State Government</div>
        <div class="partner">Sunreach Government</div>
        <div class="partner">Capital Region Government</div>
        <div class="partner">Southvale Government</div>
        <div class="partner">Top End Region Government</div>
        <div class="partner">Eastport Emergency Office</div>
      </div>
      <div class="partners-box">
        <span class="headline"><span class="accent">Partners in</span> development from the</span>
        <div class="reference-group"><span class="dot"></span><span>Kinship Recovery Circle</span></div>
      </div>
    </div>

    <div class="cover">
      <div class="cover-photo" role="img" aria-label="Photograph of a father holding his young daughter, both muddy, in soft brown tones"></div>
      <span class="sprig-mark" role="img" aria-label="Small green leaf sprig"></span>
      <p class="kicker">Harbourline<br>Charter for</p>
      <h1 class="headline">Community<br>Mending</h1>
      <span class="rule"></span>
      <div class="copy">
        <p>Disasters can deeply impact lives and livelihoods. Working with communities recovering from disasters is complex and challenging. Recovery is long-term, non-linear and dynamic, particularly in the context of compounding and concurrent disasters. These principles are a way to guide our efforts, our approach, our planning and our decision-making.</p>
        <p>Disaster recovery is part of emergency management, which includes the broader components of prevention, preparedness and response. Planning for recovery is integral to emergency preparation, and mitigation actions are often initiated as part of recovery.</p>
        <p>Disaster recovery includes built, environmental and economic elements, as well as individual and social wellbeing. Recovery can provide an opportunity to improve these aspects beyond previous conditions, by enhancing social and natural environments, infrastructure and economies – contributing to more resilient communities.</p>
      </div>
    </div>
  </section>

  <section class="side side-b">
    <div class="foliage foliage-1" role="img" aria-label="Green leafy branch illustration"></div>
    <div class="foliage foliage-2" role="img" aria-label="Green leafy sprig illustration"></div>
    <div class="foliage foliage-3" role="img" aria-label="Green leafy branch illustration"></div>

    <article class="principle p-context">
      <span class="sprig-mark" role="img" aria-label="Small green leaf sprig"></span>
      <p class="kicker">Understand</p>
      <h2 class="headline">The context:</h2>
      <p class="lead">Successful recovery is based on an understanding of the community context, with each community having its own history, values and dynamics. Recovery should:</p>
      <ul>
        <li>Acknowledge existing strengths and capacity, including past experiences and future aspirations;</li>
        <li>Appreciate the risks and stressors faced by the community;</li>
        <li>Embed accessibility, equity, inclusion and diversity in recovery practice, using culturally safe and trauma-informed approaches;</li>
        <li>Support people who may be at greater risk or disproportionately impacted;</li>
        <li>Respect and support connections to Country, environment, animals and culturally significant places and recognise environmental regeneration in recovery;</li>
        <li>Recognise pathways and time-frames vary; systems should support long-term recovery shaped by community needs; and</li>
        <li>Acknowledge the impact upon the community may extend beyond the geographical boundaries where the disaster occurred.</li>
      </ul>
    </article>

    <article class="principle p-complexity">
      <span class="sprig-mark" role="img" aria-label="Small green leaf sprig"></span>
      <p class="kicker">Recognise</p>
      <h2 class="headline">Complexity</h2>
      <p class="lead">Successful recovery is responsive to the complex and evolving nature of disasters and their impacts on communities, including compounding, cascading and concurrent events. Recovery should recognise that:</p>
      <ul>
        <li>Disasters lead to a range of effects and impacts that require a variety of approaches; they can also leave long-term legacies;</li>
        <li>Information on impacts and needs can be limited at first and changes over time;</li>
        <li>Affected individuals and the community have diverse needs, wants and expectations, which can evolve rapidly;</li>
        <li>Responsive and flexible action is crucial to addressing immediate needs;</li>
        <li>Existing community knowledge and values may challenge the assumptions of those outside of the community;</li>
        <li>Conflicting knowledge, values and priorities among individuals, the community and organisations may create tensions;</li>
        <li>Emergencies create stressful environments where grief or blame may also affect those involved; and</li>
        <li>Over time, appropriate support for individuals and communities, from within and outside, can cultivate hope and individual and collective growth.</li>
      </ul>
    </article>

    <article class="principle p-community">
      <span class="sprig-mark" role="img" aria-label="Small green leaf sprig"></span>
      <p class="kicker">Use Community<br>-Centred</p>
      <h2 class="headline">Approaches:</h2>
      <p class="lead">Successful recovery is community-centred, responsive and flexible, engaging with community and supporting them to move forward, with shared responsibilities. Recovery should:</p>
      <ul>
        <li>Assist and enable individuals, families and the community to actively participate in their own recovery;</li>
        <li>Recognise that individuals and the community may need different levels of support at various times;</li>
        <li>Be guided by the communities' priorities;</li>
        <li>Channel effort through pre-identified and existing community assets, including local knowledge, existing community strengths and resilience;</li>
        <li>Build collaborative partnerships that reflect diverse representation and community leadership in recovery;</li>
        <li>Support Aboriginal and Torres Strait Islander self-determination and Indigenous governance, recognising Country as central to recovery and resilience;</li>
        <li>Recognise that new community leaders often emerge during and after a disaster, who may not hold formal positions of authority; and</li>
        <li>Recognise that different communities may choose different paths to recovery.</li>
      </ul>
    </article>

    <article class="principle p-coordinate">
      <span class="sprig-mark" role="img" aria-label="Small green leaf sprig"></span>
      <p class="kicker">Coordinate</p>
      <h2 class="headline">All activities:</h2>
      <p class="lead">Successful recovery requires a planned, coordinated and adaptive approach, between community and partner agencies, based on continuing assessment of impacts and need. Recovery should:</p>
      <ul>
        <li>Have clearly articulated and shared goals based on desired outcomes;</li>
        <li>Be flexible, taking into account changes in community needs or stakeholder expectations;</li>
        <li>Be guided by those with experience and expertise, using skilled, authentic and capable community leadership;</li>
        <li>Be at the pace desired by the community, and seek to collaborate and reconcile different interests and time frames;</li>
        <li>Reflect well-developed community planning and information gathering before, during and after a disaster;</li>
        <li>Have clear decision-making and reporting structures and sound governance, which are transparent and accessible to the community;</li>
        <li>Demonstrate an understanding of the roles, responsibilities and authority of organisations involved and coordinate across agencies to ensure minimal service provision disruption;</li>
        <li>Be part of an emergency management approach that integrates with response operations and contributes to future prevention and preparedness; and</li>
        <li>Be inclusive, availing of and building upon relationships created before, during and after the emergency.</li>
      </ul>
    </article>

    <article class="principle p-communicate">
      <span class="sprig-mark" role="img" aria-label="Small green leaf sprig"></span>
      <p class="kicker">Communicate</p>
      <h2 class="headline">Effectively:</h2>
      <p class="lead">Successful recovery is built on effective communication between the affected community and other partners. Recovery should:</p>
      <ul>
        <li>Recognise that communication should be two-way, transparent and ongoing, building trust through shared understanding and feedback;</li>
        <li>Ensure that information is accessible to audiences in diverse situations, addresses a variety of communication needs, and is provided through a range of communication channels and networks;</li>
        <li>Establish mechanisms for coordinated and consistent communications between all service providers, organisations and individuals and the community;</li>
        <li>Ensure that all communication is relevant, timely, clear, accurate, targeted, credible and consistent; and</li>
        <li>Identify trusted sources of information and repeat key recovery messages to enable greater community confidence and receptivity.</li>
      </ul>
    </article>

    <article class="principle p-capacity">
      <span class="sprig-mark" role="img" aria-label="Small green leaf sprig"></span>
      <p class="kicker">Recognise<br>and build</p>
      <h2 class="headline">Capacity:</h2>
      <p class="lead">Successful recovery recognises, supports and builds on individual, community and organisational capacity and resilience. Recovery should:</p>
      <ul>
        <li>Assess capability and capacity requirements before, during and after a disaster;</li>
        <li>Support the development of self-reliance, preparation and disaster mitigation;</li>
        <li>Quickly identify and mobilise community skills, strengths and resources;</li>
        <li>Develop networks and partnerships to strengthen capacity, capability and resilience;</li>
        <li>Support training and knowledge sharing to sustain recovery capability across staff, volunteers, and the community;</li>
        <li>Ensure mental health and wellbeing supports are available for staff, volunteers and communities involved in disaster recovery;</li>
        <li>Recognise that resources can be provided by a range of partners and from community networks;</li>
        <li>Acknowledge that existing resources may be stretched, and that additional resources may be required;</li>
        <li>Understand that additional resources may only be available for a limited period, and that sustainability may need to be addressed;</li>
        <li>Understand when and how to step back, while continuing to support individuals and the community as a whole to be more self-sufficient when they are ready; and</li>
        <li>Monitor, evaluate and capture learning to strengthen future recovery and preparedness.</li>
      </ul>
    </article>
  </section>

</main>
</body>
</html>
```